Life Coaching Business Needs A Business card Design

Earthy, quirky, colourful business card needed for a Life Coaching company supporting same sex attracted young men. My coaching supports these same sex attracted guys to find their own inner happiness and passion and purpose and not feel they need to live a 'label' or follow the crowd. It its about personal passion and happiness.
IT IS ABOUT THEIR INNER RAINBOW.
Some aspects of rainbow would be important to the design.

I have uploaded a recently designed POSTCARD and the business card will be a smaller version with much less information. The Business Card will take the very important parts of the POSTCARD

Front of Card.......
I'm thinking the front of the card would need to be the large LOGO with a rainbow emerging from the inside...from the heart...the core. This will almost FILL the front of the card. This has been uploaded for you. IMMEDIATELY under the LOGO ( to make it a part of the logo) would be the words COACHING * WELLNESS *
The statement HAPPINESS and WHOLENESS for MEN WHO DATE MEN should feature across the front of the BUSINESS CARD as it does across the back of the POSTCARD. It will need some kind of rainbow background to the statement as it does on the POSTCARD. Needs to be a different rainbow pattern. See what you think.

That could be the front. On a black background.
I wonder what you think and what you will do with that.

Back Of Card.

I'm hoping the back of the BUSINESS card could be the PHOTO section from the back of the POSTCARD. The photo and the quote. I will make the quote shorter to fit better on a BUSINESS card. It can be written in a handwriting style to make it look like a personal message from me as it is on the POSTCARD.

All across the top of the back of the card could be the statement
MOTIVATION and INSPIRATION for MEN WHO DATE MEN

Across the card under the statement would be the three contacts
www.brightvolume.com *0437 615 203*tom@brightvolume.com

It would be great to see if you have a different idea for this arrangement.

At the bottom of the Business card ( as on the photo at on the POSTCARD ) would be my name with a description underneath

Tom Walbrook
Transformational Life Coach * Happiness Guru * Change catalyst

What do you think ? Will all of this work ?
I hope I haven't been too prescriptive. I don't want this to be a boring job for you.

Looking forward to hearing what you think and seeing what you come up with.

Target Market(s)

Same sex attracted males. All ages. Especially those who are struggling or unhappy or depressed. The card must be uplifting and it must SPEAK to these guys. I want ti include a personal 'quote' from me ( in handwriting font as if I wrote to them ) to encourage these guys to get the help they need.

Industry/Entity Type

Business

Contact Information for Business Card

I have been quite prescriptive but am happy to see what the designer might come up with as well. I don't mean to make it boring for the designer. I have included names and contact details in the brief. Please let me know if I need to give you more details.

Requirements
Must have
• LOGO
• A clear statement on the front and back to state clearly who the coaching service is for. I have explained these in the brief.
• Pic of me to fill the back of the card with room to write the details on. I have other pics if needed.
• Needs to be casual and inviting. Almost informal and organic. Quite earthy to balance with the 'lifestyle' these guys can often live.
Nice to have
• Colour and ideas to keep it uncluttered.
Should not have
• Formal design or 'business' like feel.

```html
<!DOCTYPE html>
<html lang="en">
<head>
<meta charset="utf-8">
<title>Tom Walbrook – Business Card</title>
<link href="https://fonts.googleapis.com/css2?family=Lato:wght@400;700;900&family=Kalam:wght@400&display=swap" rel="stylesheet">
<style>
  :root {
    --backdrop: #3a3c3f;
    --card: #050505;
    --ink: #1f1f1f;
    --white: #ffffff;
    --violet: #8e80c0;
    --blue: #2a8fcf;
    --teal: #2aa3b8;
    --green: #2fae4f;
    --lime: #5cb946;
    --yellow: #ecc21a;
    --amber: #f4a91b;
    --orange: #ea6a20;
    --red: #d62a2a;
    --sky-top: #f6f8f4;
    --sky-low: #e6ece6;
    --grass: #6f9a2e;
    --grass-deep: #4d7a1e;
  }
  * { box-sizing: border-box; margin: 0; padding: 0; }
  html, body { width: 1200px; height: 900px; overflow: hidden; }
  body { background: var(--backdrop); position: relative; font-family: "Lato", sans-serif; }

  .card {
    position: absolute; left: 78px; top: 122px; width: 1050px; height: 635px;
    background: var(--card); border-radius: 30px;
  }
  .audience {
    position: absolute; left: 0; right: 0; top: 40px; text-align: center;
    font-weight: 700; font-size: 29px; letter-spacing: 0.2px; white-space: nowrap;
  }
  .photo-panel {
    position: absolute; left: 112px; top: 83px; width: 818px; height: 475px; overflow: hidden;
  }
  .photo-fill {
    position: absolute; inset: 0;
    background: linear-gradient(to bottom, var(--sky-top) 0%, var(--sky-low) 72%, var(--grass) 78%, var(--grass-deep) 100%);
  }
  .contacts {
    position: absolute; left: 10px; top: 10px; font-size: 26px; color: var(--ink);
    white-space: nowrap; word-spacing: 2px;
  }
  .contacts span + span { margin-left: 14px; }
  .quote {
    position: absolute; left: 17px; top: 92px; font-family: "Kalam", cursive;
    font-size: 30px; line-height: 43px; color: #2b2b2b; white-space: nowrap;
  }
  .coach-name {
    position: absolute; left: 6px; bottom: 6px; font-weight: 900; font-size: 40px;
    color: var(--white); letter-spacing: 0.5px; -webkit-text-stroke: 1.5px #111;
    paint-order: stroke fill;
  }
  .roles {
    position: absolute; left: 0; right: 0; top: 570px; text-align: center;
    font-weight: 700; font-size: 22px; white-space: nowrap;
  }
  .c-violet { color: var(--violet); } .c-blue { color: var(--blue); } .c-teal { color: var(--teal); }
  .c-green { color: var(--green); } .c-lime { color: var(--lime); } .c-yellow { color: var(--yellow); }
  .c-amber { color: var(--amber); } .c-orange { color: var(--orange); } .c-red { color: var(--red); }
</style>
</head>
<body>
  <div class="card">
    <h1 class="audience">
      <span class="c-violet">Coaching</span>
      <span class="c-blue">and</span>
      <span class="c-green">Support</span>
      <span class="c-yellow">for</span>
      <span class="c-amber">Same Sex</span><span class="c-orange"> Attracted</span>
      <span class="c-red">Guys</span>
    </h1>

    <div class="photo-panel">
      <div class="photo-fill" role="img" aria-label="Photo of the coach standing barefoot on a grassy field under a bright sky"></div>
      <p class="contacts"><span>www.brightvolume.com</span><span>0437 615 203</span><span>tom@brightvolume.com</span></p>
      <blockquote class="quote">
        “My Coaching is about helping to change<br>
        whatever is making you unhappy or unwell.<br>
        If you’re not happy, something has to change.<br>
        If something has to change, a coach can help.”
      </blockquote>
      <h2 class="coach-name">TOM WALBROOK</h2>
    </div>

    <p class="roles">
      <span class="c-blue">Personal</span>
      <span class="c-violet">Change Coach-Relationship</span>
      <span class="c-lime">Coach-Happiness</span>
      <span class="c-amber">Guru-Equity</span>
      <span class="c-red">Advocate</span>
    </p>
  </div>
</body>
</html>
```